Roofing web site brvt roofing

Look at some of our competitors web page we like something similar with NYC roofing
https://www.quillbarroofing.example/
Maybe a skyline picture of nyc at the home page with a picture of flat roofing installation

Target Market(s)

Commercial and residential flat roofs

Industry/Entity Type

Flat Roofing industry

Coding

Coded - Design and coding required

Number of Pages Required

2 page

Font styles to use
Decorative
Script

Colors

Designer to choose colors to be used in the design.

Requirements
Must have
• At BRVT Roofing, we are a trusted and reputable roofing company specializing in new construction flat roof installation and repair. With years of experience in the industry, we take pride in providing exceptional roofing solutions to our valued clients. Our team of highly skilled and dedicated roofing professionals understands the unique challenges and requirements of new construction projects. We work closely with builders, contractors, and architects to design and install flat roofs that meet the specific needs of each project. From commercial buildings to residential complexes, we have the expertise to deliver reliable and durable roofing solutions. When it comes to flat roof repairs, we are your go-to experts. Our experienced technicians conduct thorough inspections to identify the root cause of any issues your roof may be experiencing. We utilize the latest industry techniques and high-quality materials to efficiently repair your flat roof, ensuring its integrity and longevity. At BRVT Roofing, we prioritize customer satisfaction above all else. We believe in building strong relationships with our clients by providing exceptional craftsmanship and outstanding customer service. Our team is dedicated to delivering projects on time, within budget, and to the highest standards of quality. We understand that a well-maintained roof is essential for protecting your property and ensuring the safety of its occupants. That's why we use only the best materials and employ skilled professionals who are trained in the latest roofing practices. Our commitment to excellence is evident in every project we undertake. As a fully licensed and insured roofing company, we prioritize safety and adhere to industry regulations and best practices. We take every precaution to create a safe working environment for our team and minimize any disruptions to your daily routine. When you choose BRVT Roofing, you can trust that you are working with a reliable and reputable company that will deliver exceptional results. We are committed to exceeding your expectations and providing you with a roof that is built to last. Contact us today for all your new construction flat roof installation and repair needs.
Nice to have
• NYC skyline background with commercial roofing pictures of torching roofing

```html
<!DOCTYPE html>
<html lang="en">
<head>
<meta charset="utf-8">
<title>BRVT Roofing — Flat Roof Specialists</title>
<link href="https://fonts.googleapis.com/css2?family=Oswald:wght@500;600;700&family=Roboto:wght@400;500;700&display=swap" rel="stylesheet">
<style>
:root{
  --orange:#f26522;
  --orange-deep:#e85a17;
  --ink:#222;
  --dark:#2b2728;
  --text:#666;
  --white:#fff;
  --tail:#2f2f2f;
}
*{margin:0;padding:0;box-sizing:border-box}
html,body{width:1200px;height:4062px;overflow:hidden;background:var(--white)}
body{position:relative;font-family:'Roboto',Arial,sans-serif;color:var(--ink)}
.abs{position:absolute}
.heading{font-family:'Oswald',Impact,sans-serif;font-weight:600;text-transform:uppercase;letter-spacing:-0.5px;line-height:1}
.bar-heading{padding-left:16px;border-left:4px solid var(--orange)}
.btn{position:absolute;display:flex;align-items:center;justify-content:center;font-size:14px;font-weight:500;text-transform:uppercase;background:var(--orange);color:var(--white);z-index:1}
.btn::after{content:"";position:absolute;top:0;right:-26px;width:38px;height:100%;background:var(--tail);clip-path:polygon(0 0,45% 0,100% 100%,55% 100%);z-index:-1}
.btn.light{background:var(--white);color:var(--orange)}
.btn.light::after{background:var(--tail)}
/* top bar */
.phone-top{left:145px;top:16px;font-size:25px;font-weight:500;display:flex;align-items:center;gap:12px}
.brand{left:549px;top:8px;width:99px;height:52px;border:2px solid #555;display:flex;align-items:center;justify-content:center;text-align:center;font-size:15px;line-height:1.05;color:#444;font-weight:400}
.nav{left:0;top:68px;width:1200px;height:41px;background:var(--orange)}
.nav a{position:absolute;top:12px;color:var(--white);font-size:13px;font-weight:500;text-decoration:none}
.nav a.active{top:6px;border:1.5px solid var(--white);padding:4px 10px}
/* hero */
.hero-title{left:200px;width:508px;top:444px;text-align:center;color:var(--white);font-size:56px}
.hero-sub{left:200px;width:508px;top:510px;text-align:center;color:var(--white);font-size:28px;font-weight:500}
.dot{left:1146px;width:14px;height:14px;border-radius:50%;background:#ddd}
/* about */
.about-text{left:544px;top:820px;width:513px;font-size:14.6px;line-height:26.4px;color:var(--text);text-align:justify}
/* cards */
.card{top:1419px;width:290px;height:592px;filter:drop-shadow(0 6px 10px rgba(0,0,0,.18))}
.card-shape{position:absolute;inset:0;background:var(--white);clip-path:polygon(0 0,100% 0,100% 95%,0 100%)}
.card-title{position:absolute;top:273px;left:10px;right:10px;text-align:center;font-size:18px;line-height:22px;font-weight:500}
.card-text{position:absolute;top:328px;left:40px;right:40px;font-size:13.4px;line-height:21px;color:var(--text);text-align:justify;text-align-last:center}
.arrow-btn{width:44px;height:44px;border:1.5px solid #888;border-radius:50%;top:1702px;display:flex;align-items:center;justify-content:center}
/* installs */
.installs-text{left:142px;top:2340px;width:440px;font-size:14.6px;line-height:20.5px;color:var(--white)}
input,textarea{font-family:inherit}
.field{position:absolute;background:var(--white);border:none;padding:0 20px;font-size:14px;color:#333}
.social{width:26px;height:26px;border:1.5px solid #4a6ea8;border-radius:50%;top:4012px}
</style>
</head>
<body>

<!-- header -->
<div class="abs phone-top">
  <svg width="30" height="30" viewBox="0 0 30 30"><circle cx="15" cy="15" r="15" fill="#f26522"/><path d="M10 8c1-1 2 0 3 2s0 2-1 3c1 2 3 4 5 5 1-1 1-2 3-1s3 2 2 3c-1 2-3 3-6 1-3-2-6-5-7-8-1-2 0-4 1-5z" fill="#fff"/></svg>
  555-014-2286
</div>
<div class="abs brand">BRVT<br>Roofing</div>
<div class="btn" style="left:858px;top:17px;width:165px;height:33px">Get a free quote!</div>

<nav class="abs nav">
  <a class="active" href="#" style="left:145px">HOME</a>
  <a href="#" style="left:243px">CONTACT US</a>
  <a href="#" style="left:375px">PHOTO GALLERY</a>
  <a href="#" style="left:535px">SERVICES</a>
  <a href="#" style="left:647px">ABOUT US</a>
  <svg class="abs" style="left:974px;top:12px" width="90" height="18" viewBox="0 0 90 18">
    <circle cx="7" cy="7" r="5" fill="none" stroke="#fff" stroke-width="1.8"/><line x1="11" y1="11" x2="15" y2="15" stroke="#fff" stroke-width="1.8"/>
    <path d="M34 3h3l2 9h9l2-7H38" fill="none" stroke="#fff" stroke-width="1.8"/><circle cx="40" cy="15" r="1.6" fill="#fff"/><circle cx="47" cy="15" r="1.6" fill="#fff"/>
    <circle cx="72" cy="6" r="3.5" fill="#fff"/><path d="M65 16c0-4 3-6 7-6s7 2 7 6z" fill="#fff"/>
  </svg>
</nav>

<!-- hero -->
<svg class="abs" style="left:0;top:109px" width="1200" height="560" viewBox="0 0 1200 560">
  <defs>
    <linearGradient id="sky" x1="0" y1="0" x2="0" y2="1">
      <stop offset="0" stop-color="#3f6b94"/><stop offset=".45" stop-color="#a9bccd"/><stop offset=".55" stop-color="#5c6f82"/><stop offset="1" stop-color="#5a5f66"/>
    </linearGradient>
  </defs>
  <polygon role="img" aria-label="New York skyline seen from a flat rooftop with a roofer torching membrane" points="0,0 1200,0 1057,557 0,498" fill="url(#sky)"/>
  <polygon points="323,265 694,265 752,538 0,498 0,435" fill="#f26522"/>
</svg>
<div class="abs heading hero-title">Torching Roofing</div>
<div class="abs hero-sub">Flat Roof Specialists</div>
<div class="btn light" style="left:356px;top:572px;width:164px;height:32px">Get a free quote!</div>
<div class="abs dot" style="top:539px;background:var(--orange)"></div>
<div class="abs dot" style="top:561px"></div>
<div class="abs dot" style="top:581px"></div>
<div class="abs dot" style="top:602px"></div>

<!-- about -->
<div class="abs" role="img" aria-label="Roofer working on orange clay tile roof" style="left:144px;top:710px;width:357px;height:485px;background:linear-gradient(160deg,#d96a3c,#b64d2c 60%,#8a3a22)"></div>
<div class="abs" role="img" aria-label="Tiled roof with skylight" style="left:136px;top:750px;width:170px;height:180px;border:8px solid #fff;border-left:none;background:linear-gradient(180deg,#c9623a,#a84a2a 60%,#4a78c4)"></div>
<div class="abs" role="img" aria-label="Hammer breaking old roofing stone" style="left:90px;top:938px;width:200px;height:123px;background:linear-gradient(135deg,#b4a797,#7c6c5d)"></div>
<div class="abs" role="img" aria-label="Scraping damaged roof surface" style="left:85px;top:1074px;width:205px;height:153px;background:linear-gradient(135deg,#8f8a84,#d7d2cb)"></div>
<h2 class="abs heading bar-heading" style="left:544px;top:742px;font-size:56px">About Us</h2>
<p class="abs about-text">At BRVT Roofing, we are a trusted and reputable roofing company specializing in new construction flat roof installation and repair. With years of experience in the industry, we take pride in providing exceptional roofing solutions to our valued clients. Our team of highly skilled and dedicated roofing professionals understands the unique challenges and requirements of new construction projects. We work closely with builders, contractors, and architects to design and install flat roofs that meet the specific needs of each project. From commercial buildings to residential complexes, we have the expertise to deliver reliable and durable roofing solutions. When it comes to flat roof repairs, we are your go-to experts. Our experienced technicians conduct thorough inspections to identify the root cause of any issues your roof may be experiencing.</p>
<div class="btn" style="left:544px;top:1131px;width:120px;height:33px">Read more</div>

<!-- services -->
<h2 class="abs heading bar-heading" style="left:503px;top:1316px;font-size:56px">Services</h2>
<div class="abs arrow-btn" style="left:76px"><svg width="14" height="18"><path d="M10 2L3 9l7 7" fill="none" stroke="#555" stroke-width="2"/></svg></div>
<div class="abs arrow-btn" style="left:1079px"><svg width="14" height="18"><path d="M4 2l7 7-7 7" fill="none" stroke="#555" stroke-width="2"/></svg></div>

<div class="abs card" style="left:145px">
  <div class="card-shape"></div>
  <div class="abs" role="img" aria-label="Metal standing seam roof under cloudy sky" style="left:0;top:0;width:290px;height:265px;background:linear-gradient(180deg,#9aa3ab,#c9c2b3 45%,#6f8a8a);clip-path:polygon(0 0,100% 0,100% 83%,0 100%)"></div>
  <div class="card-title">RELIABLE ROOFING<br>PROFESSIONALS</div>
  <p class="card-text">As specialists in residential and commercial roofing services, we are dedicated to providing customer service that is second to none. Whether you have a new construction project or it is time for repairs, we offer the roofing services you need.</p>
  <div class="btn" style="left:71px;top:514px;width:120px;height:32px">Read more</div>
</div>
<div class="abs card" style="left:456px">
  <div class="card-shape"></div>
  <div class="abs" role="img" aria-label="Dark asphalt shingle roof" style="left:0;top:0;width:290px;height:265px;background:linear-gradient(180deg,#d9dcdf,#b8bcc1 35%,#3d3f44);clip-path:polygon(0 0,100% 0,100% 83%,0 100%)"></div>
  <div class="card-title">INDIVIDUALIZED ROOFING<br>OPTIONS</div>
  <p class="card-text">We provide a full consultation to explain your available options so that you can choose the roofing plan that's right for your home or business. We will work with you and adhere to your personal needs, and then we'll be in contact through the whole project.</p>
  <div class="btn" style="left:71px;top:514px;width:120px;height:32px">Read more</div>
</div>
<div class="abs card" style="left:765px">
  <div class="card-shape"></div>
  <div class="abs" role="img" aria-label="Gloved hands installing roof panel" style="left:0;top:0;width:290px;height:265px;background:linear-gradient(135deg,#c0392b,#7f8c8d 40%,#a9c7c0);clip-path:polygon(0 0,100% 0,100% 83%,0 100%)"></div>
  <div class="card-title">SATISFACTION<br>GUARANTEED</div>
  <p class="card-text">We strive to save you both time and money by combining roofing knowledge, the highest quality parts and equipment, and dedication to delivering exceptional service. We will not leave the job until it is finished and you are satisfied with the results.</p>
  <div class="btn" style="left:71px;top:514px;width:120px;height:32px">Read more</div>
</div>

<!-- perfect installs -->
<svg class="abs" style="left:0;top:2090px" width="1200" height="559" viewBox="0 0 1200 559">
  <defs><linearGradient id="wood" x1="0" y1="0" x2="1" y2="1"><stop offset="0" stop-color="#3c5a2f"/><stop offset=".5" stop-color="#a07a4e"/><stop offset="1" stop-color="#6e4e33"/></linearGradient></defs>
  <rect role="img" aria-label="Roofer nailing wooden shingles" x="0" y="0" width="1200" height="559" fill="url(#wood)"/>
  <polygon points="0,0 528,0 651,233 378,559 0,559" fill="#f26522"/>
</svg>
<h2 class="abs heading bar-heading" style="left:142px;top:2268px;font-size:56px;color:#fff;border-color:#fff">Perfect Installs</h2>
<p class="abs installs-text">Your roof is your main defense against the elements. Let us walk you through the best options to fit your needs and once you feel comfortable with your choice, we'll handle the complete installation.</p>
<div class="btn light" style="left:142px;top:2429px;width:147px;height:31px">Read more</div>

<!-- newsletter -->
<h2 class="abs heading bar-heading" style="left:144px;top:2740px;font-size:55px;line-height:56px">Flat Roof Installation Roof Repair<br>Storm Damage Insurance Specialists</h2>
<p class="abs" style="left:144px;top:2879px;font-size:18px;color:#333">Sign up to receive maintenance reminders and hear about our latest projects.</p>
<div class="field" style="left:144px;top:2954px;width:424px;height:35px;border:2px solid #ccc;display:flex;align-items:center;font-size:12px;color:#888">Enter Email</div>
<div class="btn" style="left:568px;top:2954px;width:90px;height:35px">Sign up</div>

<svg class="abs" style="left:421px;top:2914px" width="779" height="500" viewBox="0 0 779 500">
  <defs><linearGradient id="patio" x1="0" y1="0" x2="0" y2="1"><stop offset="0" stop-color="#3a3d44"/><stop offset=".55" stop-color="#565a60"/><stop offset="1" stop-color="#6b4a36"/></linearGradient></defs>
  <polygon role="img" aria-label="Modern terrace with outdoor sofa and grill" points="0,130 779,0 779,500 0,500" fill="url(#patio)"/>
</svg>
<div class="abs" style="left:0;top:3044px;width:421px;height:370px;background:var(--orange)"></div>
<h2 class="abs heading" style="left:144px;top:3134px;font-size:53px;line-height:54px;color:#fff">Call Today<br>For A Free<br>Quote!</h2>
<div class="btn light" style="left:144px;top:3327px;width:170px;height:32px">Get a free quote!</div>

<!-- quote form -->
<div class="abs" style="left:0;top:3414px;width:1200px;height:571px;background:var(--dark)"></div>
<svg class="abs" style="left:0;top:3414px" width="42" height="571"><polygon points="0,0 40,571 0,571" fill="#f26522"/></svg>
<h2 class="abs heading bar-heading" style="left:427px;top:3500px;font-size:54px;color:#fff">Get A Free Quote</h2>
<svg class="abs" style="left:368px;top:3607px" width="44" height="44"><circle cx="22" cy="22" r="20" fill="none" stroke="#f26522" stroke-width="2"/><path d="M16 14c1-1 2 0 3 2s0 2-1 3c1 2 2 3 4 4 1-1 1-2 3-1s2 2 1 3c-1 1-3 2-5 1-3-2-5-4-6-7 0-2 0-3 1-5z" fill="#f26522"/></svg>
<div class="abs" style="left:424px;top:3612px;color:#fff;font-size:14px;line-height:18px">Phone<br>555-014-2286</div>
<div class="abs" style="left:558px;top:3606px;width:1px;height:44px;background:#777"></div>
<svg class="abs" style="left:599px;top:3607px" width="44" height="44"><circle cx="22" cy="22" r="20" fill="none" stroke="#f26522" stroke-width="2"/><path d="M22 11v11l7 5" fill="none" stroke="#f26522" stroke-width="2"/></svg>
<div class="abs" style="left:656px;top:3612px;color:#fff;font-size:14px;line-height:18px">Monday - Friday: 8am - 5pm<br>Saturday - Sunday: 8am-12</div>
<div class="field" style="left:162px;top:3698px;width:286px;height:43px;display:flex;align-items:center">Enter Name</div>
<div class="field" style="left:457px;top:3698px;width:284px;height:43px;display:flex;align-items:center">Enter Email</div>
<div class="field" style="left:751px;top:3698px;width:287px;height:43px;display:flex;align-items:center">Phone</div>
<div class="field" style="left:162px;top:3753px;width:876px;height:82px;padding-top:14px">Message</div>
<div class="btn" style="left:501px;top:3859px;width:168px;height:31px">Submit message</div>

<!-- footer -->
<p class="abs" style="left:144px;top:4017px;font-size:13px;color:#333">Copyright © 2024 Bravetta Construction Roofing - All Rights Reserved.</p>
<div class="abs social" style="left:903px"></div>
<div class="abs social" style="left:935px"></div>
<div class="abs social" style="left:966px"></div>
<div class="abs social" style="left:998px"></div>
<div class="abs social" style="left:1029px"></div>

</body>
</html>
```